Amber Vital 480

This is a 9 week program we conduct in our gym/recovery facility with the aim of educating members on the ins and outs of training, sauna use, cold plunge, sleep and lifestyle factors that they need to consider to increase health span into their older age. It is geared towards the Gen X age group.

```html
<!DOCTYPE html>
<html lang="en">
<head>
<meta charset="utf-8">
<title>Amber Vital 480 — A 9-Week Journey to Longevity</title>
<link href="https://fonts.googleapis.com/css2?family=Andika:wght@400;700&family=Open+Sans:wght@400;600;700&display=swap" rel="stylesheet">
<style>
  :root{
    --brand:#15a2dc;
    --brand-dark:#0d86b8;
    --ink:#1a1a1a;
    --body:#3d3d3d;
    --tint:#eff5fd;
    --line:#e3e9f1;
    --white:#ffffff;
    --photo-green:#6f8f4a;
    --photo-warm:#c9a48e;
    --photo-wood:#b98a5c;
    --photo-skin:#6b4a35;
  }
  *{box-sizing:border-box;margin:0;padding:0}
  html,body{width:1200px;height:3297px;overflow:hidden;background:var(--white)}
  body{position:relative;font-family:"Open Sans",sans-serif;color:var(--body)}
  .abs{position:absolute}
  .display{font-family:"Andika",sans-serif;color:var(--ink);font-weight:400}
  .accent{color:var(--brand)}
  .btn{position:absolute;display:flex;align-items:center;justify-content:center;border-radius:24px;
       background:linear-gradient(90deg,var(--brand-dark),var(--brand));color:var(--white);
       font-weight:700;font-size:15px;text-decoration:none}
  .para{font-size:16px;line-height:27.5px;color:var(--body)}

  /* header & hero */
  .hero-band{left:0;top:0;width:1200px;height:471px;background:var(--tint)}
  .logo{font-family:"Andika",sans-serif;color:var(--brand);font-size:31px;line-height:1}
  .nav{left:544px;top:40px;display:flex;gap:32px;font-size:16px}
  .nav a{color:var(--body);text-decoration:none}
  .nav a.active{color:var(--brand);font-weight:600}
  .hero-title{left:0;width:1200px;top:112px;text-align:center;font-size:41px;line-height:47px}
  .hero-sub{left:0;width:1200px;top:224px;text-align:center;font-size:21px;color:var(--ink)}
  .hero-text{left:320px;width:560px;top:260px;text-align:center;font-size:15.5px;line-height:28px;color:var(--body)}
  .photo-left{left:0;top:358px;width:780px;height:282px;border-radius:0 170px 170px 0;
       background:linear-gradient(120deg,#8fae5d,var(--photo-green) 45%,#a7b8c9)}
  .photo-right{left:832px;top:358px;width:368px;height:193px;border-radius:100px 0 0 100px;
       background:linear-gradient(120deg,#8d8a86,var(--photo-warm) 55%,#8e5d58)}

  /* about */
  .h2{font-size:43px;line-height:50px}
  .about-frame{left:690px;top:750px;width:380px;height:325px;border-radius:18px;background:var(--tint)}
  .about-photo{left:707px;top:736px;width:381px;height:322px;border-radius:14px;
       background:linear-gradient(135deg,#a9c46a,#6f9a4c 50%,#c7a48c)}

  /* services */
  .card{position:absolute;top:1269px;width:307px;height:480px;border-radius:14px;background:var(--tint);overflow:hidden}
  .card-img{position:absolute;left:0;top:0;width:307px;height:205px}
  .card-img svg{position:absolute;left:0;bottom:0}
  .card .week{position:absolute;left:26px;top:227px;font-size:16px;color:var(--ink)}
  .card h3{position:absolute;left:26px;top:253px;font-family:"Andika",sans-serif;font-weight:400;font-size:25px;color:var(--brand)}
  .card p{position:absolute;left:26px;top:303px;width:260px;font-size:15.5px;line-height:27.5px;color:var(--body)}
  .arrow{top:1498px}

  /* advantage */
  .adv-shape{left:832px;top:1893px;width:368px;height:250px;border-radius:40px 0 0 40px;background:var(--tint)}
  .feature{position:absolute;left:707px;width:311px;height:64px;border:1px solid var(--line);border-radius:12px;
       background:var(--white);box-shadow:0 2px 6px rgba(20,60,110,.06);display:flex;align-items:center}
  .feature svg{margin-left:38px;width:38px;height:38px}
  .feature span{position:absolute;left:116px;font-size:19.5px;color:var(--ink)}

  /* faq */
  .faq-item{position:absolute;left:230px;width:740px;height:64px;border:1px solid var(--line);border-radius:14px;
       background:var(--white);box-shadow:0 2px 6px rgba(20,60,110,.05);display:flex;align-items:center;
       padding-left:30px;font-size:16px;font-weight:600;color:var(--ink)}
  .faq-item.open{background:var(--tint)}
  .faq-answer{left:263px;top:2680px;width:660px;font-size:16px;line-height:27.5px;color:var(--body)}

  /* footer */
  .footer{left:0;top:3093px;width:1200px;height:204px;background:var(--tint)}
  .footer-links{left:0;width:1200px;top:3188px;display:flex;justify-content:center;gap:32px;font-size:16px}
  .footer-links a{color:var(--body);text-decoration:none}
  .copy{left:0;width:1200px;top:3227px;text-align:center;font-size:15.5px;color:var(--body)}
</style>
</head>
<body>

<!-- Header & Hero -->
<div class="abs hero-band"></div>
<div class="abs logo" style="left:111px;top:35px">Amber Vital 480</div>
<nav class="abs nav">
  <a href="#" class="active">Home</a><a href="#">About</a><a href="#">Services</a><a href="#">Blog</a><a href="#">Contact</a>
</nav>
<a href="#" class="btn" style="left:953px;top:28px;width:135px;height:46px">Get Started</a>

<h1 class="abs display hero-title">Transform Your Health Span<br>with <span class="accent">Amber Vital 480</span></h1>
<p class="abs hero-sub">A 9-Week Journey to Longevity</p>
<p class="abs hero-text">Train smarter, recover better, sleep deeper. Amber Vital 480 is your path to a longer, healthier life.</p>
<div class="abs photo-left" role="img" aria-label="Photo of older adults stretching outdoors with a coach"></div>
<div class="abs photo-right" role="img" aria-label="Photo of a woman relaxing on a sofa with a blanket"></div>

<!-- About -->
<h2 class="abs display h2" style="left:111px;top:725px">About <span class="accent">Us</span></h2>
<p class="abs para" style="left:111px;top:789px;width:500px">Lorem ipsum dolor sit amet, consectetur adipiscing elit, sed iusmod tempor incididunt ut labore et dolore magna aliqua. Quis ipsum sus pendisse ultrices gravida. Risus commodo viverra maecs accumsan lacus vel facilisis.</p>
<p class="abs para" style="left:111px;top:908px;width:500px">Lorem ipsum dolor sit amet, consectetur adipiscing elit, sed iusmod tempor incididunt ut labore et dolore magna aliqua. Quis ipsum sus pendisse ultrices gravida. Risus commodo viverra ma.</p>
<a href="#" class="btn" style="left:111px;top:1018px;width:135px;height:45px">Learn More</a>
<div class="abs about-frame"></div>
<div class="abs about-photo" role="img" aria-label="Photo of a smiling couple riding bicycles in a park"></div>

<!-- Services -->
<h2 class="abs display h2" style="left:0;width:1200px;top:1169px;text-align:center">Our <span class="accent">Services</span></h2>

<svg class="abs arrow" style="left:54px" width="26" height="20" viewBox="0 0 26 20" fill="none" stroke="#15a2dc" stroke-width="2"><path d="M24 10H3M9 4 3 10l6 6"/></svg>
<svg class="abs arrow" style="left:1116px" width="26" height="20" viewBox="0 0 26 20" fill="none" stroke="#15a2dc" stroke-width="2"><path d="M2 10h21M17 4l6 6-6 6"/></svg>

<article class="card" style="left:111px">
  <div class="card-img" role="img" aria-label="Photo of a woman in a robe resting in a sauna" style="background:linear-gradient(135deg,var(--photo-wood),#d8b58f 60%,#eee)">
    <svg width="307" height="50" viewBox="0 0 307 50" preserveAspectRatio="none"><path d="M0 6C80 52 230 48 307 0V50H0Z" fill="#eff5fd"/></svg>
  </div>
  <div class="week">Week 1</div>
  <h3>Sauna Therapy</h3>
  <p>Lorem ipsum dolor sit acsectetur adipiscing elit, sed do eiusmod tempor incididunt ut labore et dolore magna aliqua. Quis ipsum suspendisse ultrices gravida.</p>
</article>

<article class="card" style="left:446px">
  <div class="card-img" role="img" aria-label="Photo of a man smiling in a cold plunge bath" style="background:linear-gradient(135deg,#7d9a5a,var(--photo-skin) 55%,#c9d8e2)">
    <svg width="307" height="50" viewBox="0 0 307 50" preserveAspectRatio="none"><path d="M0 6C80 52 230 48 307 0V50H0Z" fill="#eff5fd"/></svg>
  </div>
  <div class="week">Week 2</div>
  <h3>Cold Plunge</h3>
  <p>Lorem ipsum dolor sit acsectetur adipiscing elit, sed do eiusmod tempor incididunt ut labore et dolore magna aliqua. Quis ipsum suspendisse ultrices gravida.</p>
</article>

<article class="card" style="left:780px">
  <div class="card-img" role="img" aria-label="Photo of a woman napping in a deck chair on a lawn" style="background:linear-gradient(160deg,#4f7a2e,#7aa53c 55%,#3f6a24)">
    <svg width="307" height="50" viewBox="0 0 307 50" preserveAspectRatio="none"><path d="M0 6C80 52 230 48 307 0V50H0Z" fill="#eff5fd"/></svg>
  </div>
  <div class="week">Week 3</div>
  <h3>Sleep Optimization</h3>
  <p>Lorem ipsum dolor sit acsectetur adipiscing elit, sed do eiusmod tempor incididunt ut labore et dolore magna aliqua. Quis ipsum suspendisse ultrices gravida.</p>
</article>

<!-- Advantage -->
<h2 class="abs display h2" style="left:111px;top:1858px">The Amber Vital<br><span class="accent">Advantage</span></h2>
<p class="abs para" style="left:111px;top:1970px;width:500px">Lorem ipsum dolor sit amet, consectetur adipiscing elit, sed iusmod tempor incididunt ut labore et dolore magna aliqua. Quis ipsum sus pendisse ultrices gravida. Risus commodo viverra maecs accumsan lacus vel facilisis.</p>
<p class="abs para" style="left:111px;top:2088px;width:510px">Sed iusmod tempor incididunt ut labore et dolore magna aliqua. Quis ipsum sus pendisse ultrices gravius commodo viverra maeccumsan.</p>
<a href="#" class="btn" style="left:111px;top:2168px;width:135px;height:45px">Learn More</a>

<div class="abs adv-shape"></div>
<div class="feature" style="top:1865px">
  <svg viewBox="0 0 38 38" fill="none" stroke="#2a3a55" stroke-width="1.4"><circle cx="19" cy="9" r="4"/><path d="M12 22c2-6 12-6 14 0M9 30h20M13 22l-3 8M25 22l3 8" /><path d="M19 2v3" stroke="#15a2dc"/></svg>
  <span>Tailored to You</span>
</div>
<div class="feature" style="top:1945px">
  <svg viewBox="0 0 38 38" fill="none" stroke="#2a3a55" stroke-width="1.4"><path d="M19 4c-6 3-7 10 0 14 7-4 6-11 0-14z" stroke="#15a2dc"/><path d="M6 22h10l6 4H10M22 26v8"/></svg>
  <span>Holistic Approach</span>
</div>
<div class="feature" style="top:2025px">
  <svg viewBox="0 0 38 38" fill="none" stroke="#2a3a55" stroke-width="1.4"><circle cx="19" cy="14" r="3.5"/><circle cx="10" cy="20" r="3"/><circle cx="28" cy="20" r="3"/><path d="M13 30c0-5 12-5 12 0M5 32c0-4 10-4 10 0M23 32c0-4 10-4 10 0"/><path d="M19 3l1 2 2 .3-1.5 1.4.4 2-1.9-1-1.9 1 .4-2L16 5.3 18 5z" stroke="#15a2dc"/></svg>
  <span>Expert Coaches</span>
</div>
<div class="feature" style="top:2104px">
  <svg viewBox="0 0 38 38" fill="none" stroke="#2a3a55" stroke-width="1.4"><circle cx="19" cy="19" r="15"/><circle cx="19" cy="19" r="10"/><path d="M14 19l4 4 7-8" stroke="#15a2dc" stroke-width="1.8"/></svg>
  <span>Proven Results</span>
</div>

<!-- FAQ -->
<h2 class="abs display h2" style="left:0;width:1200px;top:2333px;text-align:center">Frequently Asked <span class="accent">Questions</span></h2>
<p class="abs" style="left:300px;width:600px;top:2411px;text-align:center;font-size:15.5px;line-height:28px">Sed iusmod tempor incididunt ut labore et dolore magna aliqua. Quis ipsum sus pendisse ultrices gravius commodo viverra maeccumsan.</p>

<div class="faq-item" style="top:2507px">1. Lorem ipsum dolor sit amet, consectetur adipiscing elit, sed do eiusmod ?</div>
<div class="faq-item open" style="top:2591px">2. Lorem ipsum dolor sit amet, consectetur adipiscing elit, sed do eiusmod ?</div>
<p class="abs faq-answer">Lorem ipsum dolor sit amet, consectetur adipiscing elit, sed do eiusmod tempor incididunt ut labore et dolore magna aliqua. Quis ipsum suspendisse ultrices gravida. Risus commodo viverra maecenas accumsan lacus vel facilisis.</p>
<div class="faq-item" style="top:2786px">3. Lorem ipsum dolor sit amet, consectetur adipiscing elit, sed do eiusmod ?</div>
<div class="faq-item" style="top:2869px">4. Lorem ipsum dolor sit amet, consectetur adipiscing elit, sed do eiusmod ?</div>
<div class="faq-item" style="top:2955px">4. Lorem ipsum dolor sit amet, consectetur adipiscing elit, sed do eiusmod ?</div>

<!-- Footer -->
<footer class="abs footer"></footer>
<div class="abs logo" style="left:0;width:1200px;text-align:center;top:3138px;font-size:33px">Amber Vital 480</div>
<nav class="abs footer-links"><a href="#">Home</a><a href="#">About</a><a href="#">Services</a><a href="#">Blog</a><a href="#">Contact</a></nav>
<p class="abs copy">2024 Amber Vital 480. All Rights Reserved</p>

</body>
</html>
```